Cat-products company needs smart, yet endearing, business card

We need a business card design for a new, but up-and-running, business based in Honolulu, Hawaii. The business is Purrnest Nook Co. Our first product is the most environmentally-friendly cat grass kit ever seen on the planet. Future products, currently in the R&D phase, will include a variety of exciting cat scratchers. We also do consulting work to help apartment-dwellers make their home more cat-friendly and, in the future, plan on doing full, custom installs of structure to create high walkways for cats.

Target Market(s)

Middle-aged, apartment-dwelling, middle-class workers who own 1 or more cats and who dote on them.

Industry/Entity Type

Pet Care

Contact Information for Business Card

A striking, professional, yet warm and friendly design is what we're after.

Font styles to use
Serif
Sans Serif
Other font styles liked:
• Comfortaa

Colors

Designer to choose colors to be used in the design.

Requirements
Must have
• The company logo: (see attachment)
• The company name: Purrnest Nook Co
• The web address: www.purrnestnookco.com
• Email: support@purrnestnookco.com
• Phone: +1 (808) 571 6023
• Update (Fri Jun 30 3017 7:45pm Hawaii Time) I would like, is possible, uploaded picture of the cat grass kit on the back of the card with some text along the lines of: Purrnest Nook Co - Maker Of The Leafiest Feline Sprout Set Yet
Nice to have
• A cat picture, cartoon, real or silhouette that illustrates cats in action and/or relaxing; ie using the apartment space to live, play and relax in and being well-contented.
• Most of the website is done in the font: Comfortaa. It might be nice to continue using this for brand consistency.
Should not have
• Hard-to-read fonts.

```html
<!DOCTYPE html>
<html lang="en">
<head>
<meta charset="utf-8">
<title>Purrnest Nook Co – Business Card</title>
<link rel="stylesheet" href="https://fonts.googleapis.com/css2?family=Open+Sans:wght@400;600;700;800&display=swap">
<style>
  :root {
    --backdrop: #8f8f8f;
    --card-white: #ffffff;
    --cocoa: #5a342e;
    --cocoa-soft: #6a423b;
    --sun: #fbb116;
    --ink: #2f2624;
  }
  * { margin: 0; padding: 0; box-sizing: border-box; }
  html, body { width: 1200px; height: 900px; overflow: hidden; }
  body {
    background: var(--backdrop);
    font-family: "Open Sans", Arial, sans-serif;
    position: relative;
  }
  .card {
    position: absolute;
    top: 306px;
    width: 440px;
    height: 271px;
    border-radius: 10px;
    overflow: hidden;
  }
  .card--front { left: 149px; background: var(--card-white); }
  .card--back { left: 608px; background: var(--cocoa); }

  .brand-name {
    position: absolute;
    left: 24px;
    top: 30px;
    font-weight: 800;
    font-size: 32px;
    line-height: 36px;
    color: var(--sun);
  }
  .brand-square {
    position: absolute;
    left: 243px;
    top: 96px;
    width: 150px;
    height: 150px;
    background: var(--cocoa);
    border-radius: 3px;
  }
  .person {
    position: absolute;
    left: 24px;
    top: 151px;
  }
  .person__name {
    font-weight: 700;
    font-size: 15px;
    color: var(--sun);
    letter-spacing: 0.2px;
  }
  .person__role {
    font-size: 11.5px;
    color: var(--ink);
    margin-top: 1px;
  }
  .contact {
    position: absolute;
    left: 24px;
    top: 200px;
    list-style: none;
  }
  .contact__item {
    display: flex;
    align-items: center;
    gap: 5px;
    font-size: 11.5px;
    line-height: 16px;
    color: var(--ink);
  }
  .contact__icon { width: 9px; height: 9px; flex: none; }

  .back-texture {
    position: absolute;
    inset: 0;
    background: radial-gradient(ellipse at center, var(--cocoa) 30%, var(--cocoa-soft) 100%);
    opacity: 0.6;
  }
  .back-mark {
    position: absolute;
    left: 182px;
    top: 46px;
    width: 76px;
    height: 76px;
    border-radius: 50%;
    background: var(--card-white);
  }
  .back-name {
    position: absolute;
    left: 0;
    right: 0;
    top: 148px;
    text-align: center;
    font-weight: 800;
    font-size: 32px;
    line-height: 36px;
    color: var(--sun);
  }
</style>
</head>
<body>
  <section class="card card--front" aria-label="Business card front">
    <div class="brand-name">Purrnest<br>Nook Co</div>
    <div class="brand-square" aria-hidden="true"></div>
    <div class="person">
      <p class="person__name">LEILANI KAHALE</p>
      <p class="person__role">Managing Director</p>
    </div>
    <ul class="contact">
      <li class="contact__item">
        <svg class="contact__icon" viewBox="0 0 10 10" aria-hidden="true"><path fill="#fbb116" d="M2 0.5 L3.6 2.8 L2.7 3.8 Q3.8 6 6.2 7.3 L7.2 6.4 L9.5 8 L8.3 9.6 Q4.5 9.4 2 6.8 Q0.3 4.6 0.4 1.6 Z"/></svg>
        +1 (808) 571 6023
      </li>
      <li class="contact__item">
        <svg class="contact__icon" viewBox="0 0 10 10" aria-hidden="true"><rect x="0.5" y="2" width="9" height="6.4" rx="0.8" fill="#fbb116"/><path d="M0.8 2.4 L5 5.6 L9.2 2.4" fill="none" stroke="#fff" stroke-width="0.9"/></svg>
        support@purrnestnookco.com
      </li>
      <li class="contact__item">
        <svg class="contact__icon" viewBox="0 0 10 10" aria-hidden="true"><circle cx="5" cy="5" r="4.5" fill="#fbb116"/><path d="M0.8 5 H9.2 M5 0.6 Q2.6 5 5 9.4 M5 0.6 Q7.4 5 5 9.4" fill="none" stroke="#fff" stroke-width="0.7"/></svg>
        www.purrnestnookco.com
      </li>
    </ul>
  </section>

  <section class="card card--back" aria-label="Business card back">
    <div class="back-texture" role="img" aria-label="Soft repeating brand pattern in a darker cocoa tone"></div>
    <div class="back-mark" aria-hidden="true"></div>
    <p class="back-name">Purrnest<br>Nook Co</p>
  </section>
</body>
</html>
```